BRISKEL Need a luxury modern business card designed.

Need a luxury modern business card designed. refer to the uploaded files for the company name and logo in the zip file under source files. i will making my descion on monday. so please send in before then so if we need to edit we will have the time. we have a trade show coming up and im on a deadline for printer.

Target Market(s)

high end clients

Contact Information for Business Card

Company nAme and logo. Tobias Fennick Co-Founder / Project Manager Office # 555-318-7094 Cell # 555-642-1586 BRISKEL.CA Tobias@briskel-example.ca

Font styles to use
Other font styles liked:
• Modern

Requirements
Must have
• Company name and logo, contact info, using the black, gold and white color scheme.

```html
<!DOCTYPE html>
<html lang="en">
<head>
<meta charset="utf-8">
<title>Briskel Business Card</title>
<link href="https://fonts.googleapis.com/css2?family=Raleway:wght@700&family=Arimo:wght@400&display=swap" rel="stylesheet">
<style>
  :root {
    --backdrop: #7b7b7b;
    --paper: #ffffff;
    --charcoal: #2e2e2e;
    --ink: #1f1f1f;
    --gold: #9a8b55;
    --rule: #8a8a8a;
    --muted: #6b6b6b;
  }
  html, body {
    margin: 0;
    width: 1200px;
    height: 1200px;
    overflow: hidden;
    background: var(--backdrop);
  }
  .canvas {
    position: relative;
    width: 1200px;
    height: 1200px;
  }
  .card {
    position: absolute;
    top: 310px;
    width: 365px;
    height: 595px;
    box-shadow: 2px 3px 6px rgba(0,0,0,0.35);
  }
  .card--front { left: 234px; background: var(--paper); }
  .card--back  { left: 627px; width: 370px; background: var(--charcoal); }

  .company-name {
    position: absolute;
    left: 0;
    width: 100%;
    text-align: center;
    font-family: "Raleway", sans-serif;
    font-weight: 700;
    font-size: 38px;
    letter-spacing: 0.02em;
    line-height: 1;
  }
  .card--front .company-name { top: 212px; color: var(--ink); }
  .card--back .company-name  { top: 268px; color: var(--paper); }

  .company-line {
    position: absolute;
    left: 0;
    width: 100%;
    text-align: center;
    font-family: "Arimo", sans-serif;
    font-size: 13px;
    line-height: 1;
  }
  .card--front .company-line { top: 258px; color: var(--muted); }
  .card--back .company-line  { top: 316px; color: var(--paper); }

  .contact-name {
    position: absolute;
    top: 373px;
    width: 100%;
    text-align: center;
    font-family: "Raleway", sans-serif;
    font-weight: 700;
    font-size: 20px;
    color: var(--gold);
  }
  .contact-role {
    position: absolute;
    top: 399px;
    width: 100%;
    text-align: center;
    font-family: "Arimo", sans-serif;
    font-size: 16.5px;
    color: var(--ink);
  }
  .icon-row {
    position: absolute;
    top: 441px;
    left: 50%;
    transform: translateX(-50%);
    display: flex;
    align-items: center;
    gap: 4px;
  }
  .icon-row .rule { width: 50px; height: 1px; background: var(--rule); margin: 0 6px; }
  .icon {
    width: 25px;
    height: 25px;
    background: var(--gold);
    display: flex;
    align-items: center;
    justify-content: center;
  }
  .details {
    position: absolute;
    top: 478px;
    width: 100%;
    text-align: center;
    font-family: "Arimo", sans-serif;
    font-size: 16.5px;
    line-height: 21px;
    color: var(--ink);
  }
</style>
</head>
<body>
<main class="canvas">
  <section class="card card--front">
    <div class="company-name">BRISKEL</div>
    <div class="company-line">Luxury Landscapes</div>
    <div class="contact-name">TOBIAS FENNICK</div>
    <div class="contact-role">Co-Founder / Project Manager</div>
    <div class="icon-row">
      <span class="rule"></span>
      <span class="icon" aria-label="office phone">
        <svg width="17" height="15" viewBox="0 0 17 15"><path d="M1 5 Q8.5 0 16 5 L14 7 L12 5.5 L12 4 Q8.5 3 5 4 L5 5.5 L3 7 Z" fill="#fff"/><rect x="4" y="8" width="9" height="6" rx="1" fill="#fff"/></svg>
      </span>
      <span class="icon" aria-label="mobile phone">
        <svg width="10" height="16" viewBox="0 0 10 16"><rect x="1" y="0.8" width="8" height="14.4" rx="1.5" fill="none" stroke="#fff" stroke-width="1.5"/><rect x="3" y="3" width="4" height="7.5" fill="#fff"/></svg>
      </span>
      <span class="icon" aria-label="email">
        <svg width="15" height="11" viewBox="0 0 15 11"><rect x="0.7" y="0.7" width="13.6" height="9.6" fill="none" stroke="#fff" stroke-width="1.3"/><path d="M0.7 0.7 L7.5 6 L14.3 0.7" fill="none" stroke="#fff" stroke-width="1.3"/></svg>
      </span>
      <span class="rule"></span>
    </div>
    <div class="details">
      555-318-7094<br>
      555-642-1586<br>
      briskel.ca tobias@briskel-example.ca
    </div>
  </section>

  <section class="card card--back">
    <div class="company-name">BRISKEL</div>
    <div class="company-line">Luxury Landscapes</div>
  </section>
</main>
</body>
</html>
```